Business Card Design

I already have a company logo for my company. I have a logo for the manufacturer we represent. I want a professional business card design.

```html
<!DOCTYPE html>
<html lang="en">
<head>
<meta charset="utf-8">
<title>Beacon Guard LLC – Business Card</title>
<link href="https://fonts.googleapis.com/css2?family=Michroma&family=Poppins:wght@400;500;600&display=swap" rel="stylesheet">
<style>
  :root {
    --page: #e9e9eb;
    --card: #1c1d1f;
    --red: #e3202a;
    --gold: #e0a81a;
    --white: #f4f4f4;
    --pattern-a: #2a1c1d;
    --pattern-b: #1f1a16;
  }
  * { box-sizing: border-box; margin: 0; padding: 0; }
  html, body { width: 1200px; height: 1108px; overflow: hidden; }
  body {
    background: var(--page);
    position: relative;
    font-family: "Poppins", sans-serif;
  }
  .card {
    position: absolute;
    top: 244px;
    width: 400px;
    height: 620px;
    border-radius: 22px;
    background: var(--card);
    overflow: hidden;
    box-shadow: 0 14px 30px rgba(0,0,0,.25);
  }
  .card--front { left: 150px; }
  .card--back { left: 650px; }

  .brand {
    position: absolute;
    top: 110px; left: 0; right: 0;
    display: flex; flex-direction: column; align-items: center; gap: 18px;
  }
  .brand__mark {
    width: 58px; height: 58px;
    background: var(--red);
    border-radius: 6px;
  }
  .brand__name {
    font-family: "Michroma", sans-serif;
    color: var(--white);
    font-size: 25px;
    line-height: 1.25;
    text-align: center;
    letter-spacing: 1px;
  }

  .person {
    position: absolute; top: 330px; left: 0; right: 0; text-align: center;
  }
  .person__name {
    font-family: "Michroma", sans-serif;
    color: var(--red);
    font-size: 21px;
    letter-spacing: 1px;
  }
  .person__title {
    color: var(--gold);
    font-size: 15px;
    letter-spacing: 1px;
    margin-top: 4px;
  }

  .icon-row {
    position: absolute; top: 398px; left: 50px; right: 50px;
    display: flex; align-items: center; gap: 10px;
  }
  .icon-row .rule { flex: 1; height: 1px; background: var(--gold); }
  .icon {
    width: 30px; height: 30px; border-radius: 5px;
    background: var(--red);
    display: flex; align-items: center; justify-content: center;
  }
  .icon svg { width: 18px; height: 18px; }

  .contact {
    position: absolute; top: 444px; left: 0; right: 0;
    text-align: center; color: var(--white);
    font-size: 16px; line-height: 1.55;
  }
  .contact .accent { color: var(--red); }

  .divider {
    position: absolute; top: 540px; left: 80px; right: 80px;
    height: 1px; background: var(--gold);
  }
  .address {
    position: absolute; top: 552px; left: 0; right: 0;
    text-align: center; color: var(--white);
    font-size: 15px; line-height: 1.5;
  }

  .pattern {
    position: absolute; inset: 0;
    background: linear-gradient(160deg, var(--pattern-a), var(--pattern-b) 55%, var(--pattern-a));
  }
  .back-brand {
    position: absolute; top: 50%; left: 50%;
    transform: translate(-50%, -50%);
    display: flex; align-items: center; gap: 8px;
    font-family: "Michroma", sans-serif;
    color: var(--red);
    font-size: 12px;
    white-space: nowrap;
  }
  .back-brand__mark { width: 14px; height: 14px; background: var(--red); border-radius: 2px; }
</style>
</head>
<body>
  <section class="card card--front">
    <div class="brand">
      <div class="brand__mark"></div>
      <div class="brand__name">BEACON GUARD<br>LLC</div>
    </div>

    <div class="person">
      <div class="person__name">DANIEL ROURKE</div>
      <div class="person__title">MANAGING DIRECTOR</div>
    </div>

    <div class="icon-row">
      <span class="rule"></span>
      <span class="icon" aria-label="Phone">
        <svg viewBox="0 0 24 24" fill="#fff"><path d="M6.6 10.8a15 15 0 0 0 6.6 6.6l2.2-2.2a1 1 0 0 1 1-.25 11.4 11.4 0 0 0 3.6.6 1 1 0 0 1 1 1V20a1 1 0 0 1-1 1A17 17 0 0 1 3 4a1 1 0 0 1 1-1h3.5a1 1 0 0 1 1 1c0 1.25.2 2.45.6 3.6a1 1 0 0 1-.25 1z"/></svg>
      </span>
      <span class="icon" aria-label="Email">
        <svg viewBox="0 0 24 24" fill="none" stroke="#fff" stroke-width="2"><rect x="3" y="5" width="18" height="14" rx="1"/><path d="M3 6l9 7 9-7"/></svg>
      </span>
      <span class="icon" aria-label="Website">
        <svg viewBox="0 0 24 24" fill="none" stroke="#fff" stroke-width="2"><circle cx="12" cy="12" r="9"/><path d="M3 12h18M12 3c3 3 3 15 0 18M12 3c-3 3-3 15 0 18"/></svg>
      </span>
      <span class="rule"></span>
    </div>

    <div class="contact">
      <div>044-555 210 347</div>
      <div>info@beaconguard.com</div>
      <div>www.<span class="accent">beaconguard</span>.com</div>
    </div>

    <div class="divider"></div>

    <div class="address">
      <div>88, Harbor Row Suite 4</div>
      <div>45190,Eastland</div>
    </div>
  </section>

  <section class="card card--back">
    <div class="pattern" role="img" aria-label="Faint repeating brand pattern in dark red and gold"></div>
    <div class="back-brand">
      <span class="back-brand__mark"></span>
      <span>BEACON GUARD</span>
    </div>
  </section>
</body>
</html>
```